July 2022 Industrial Manufacturer Product Expo Mexico City

We manufacture large screws and fastners for large Mining equipment, Trains, large ships, airplanes, wind turbines, and so on. We also do custom work base on the customer needs. No matter the size we can make it.
We have a Expo coming up with companies all over the world. We have to stand out we are a family own business so our customer service will be above and beyond anyone can provide. We do not have a sales force to push our products and services we provide one on one service.
Plus@!! I'm looking for anything that you designers can come up with if it was your company to put on a business card, plus i want to do a 1 or 2 sided pamphlet, and then a website. We make Speciality Bolts for large mining equipment these bolts can be 3 to 4 foot long!!! Plus fasteners, Nuts, washers, any, size, strengths, special materials, we offer more of a ono on one customer service, We are a small company, family own, but can fulfill any type of orders. We can also provide special time lines for emergency orders. "We keep the machines running we here at KRV don't believe in down time" We want to hear any slogan based on our company to stand out.
Thanks i really appreciate all your work and options that we have to pick on. Plus just a thought we could possibly want to entertain a experience Marketing internet help maybe a employment possibility. Thanks

I need 2 cards one in Spanish and English Like the steel back ground maybe send me in some bright red and blue writing Same with the Black cards Please remove the word Military The logo KRV maybe integrate a picture of a Bolt 🔩 Thank you

Still looking for I need 2 cards one in Spanish and English Like the steel back ground maybe send me in some bright red and blue writing Same with the Black cards try bright writing Please remove the word Military The logo KRV maybe integrate a picture of a Bolt 🔩 Plus will need the company to make a brochure and website next Thank you

Target Market(s)

Large Mining, Ship, Train, Green Energy, VELM, and Government equipment. Throughout the World

Industry/Entity Type

We can Custom Manufacture any type of Fastners for Mining equipment, Trains, Ships, Green energy, Governments, or military projects. wind turbines,

Contact Information for Business Card

I attached the name and contact info that's on a card, plus the Company Logo. Would like industrial looking background with Bright Colors that will stand out!! If we can insert somewhere maybe on back that we "Custom Manufacture Any Size or Quantity Fastners for Large Mining Equipment, Trains, Ships, Green Energy Equipment or Government Projects

Font styles to use
Other font styles liked:
• You Pick, has to be bold, colorful standout, Professional looking Beable to read it.

Colors

Designer to choose colors to be used in the design.

Requirements
Must have
• Need in Spanish and English TO STANDOUT FROM THE REST OF THE EXPO!! See Business card details, Rounded corners
Nice to have
• Can i see some of the darker cards with Bright Red and Blue letters I like to see the different type of card material, heavy thickness, plastic, transparent, Metal types, Bright Colors, I saw like Raised letters like on the logo.

```html
<!DOCTYPE html>
<html lang="es">
<head>
<meta charset="utf-8">
<title>KRV – Tarjetas de presentación</title>
<link rel="stylesheet" href="https://fonts.googleapis.com/css2?family=Roboto:wght@400;500;700&family=Roboto+Condensed:wght@400;700&display=swap">
<style>
  :root {
    --page: #c9c9c9;
    --white: #ffffff;
    --charcoal: #2a2a2b;
    --charcoal-light: #4a4a4c;
    --logo-grey: #4b4b4d;
    --royal: #1f3aa8;
    --sky: #1e8fd8;
    --ink-light: #f2f2f2;
    --silver: #b9babd;
  }
  html, body {
    margin: 0;
    width: 1200px;
    height: 800px;
    overflow: hidden;
    background: var(--page);
    font-family: "Roboto", sans-serif;
  }
  .canvas {
    position: relative;
    width: 1200px;
    height: 800px;
  }
  .card {
    position: absolute;
    top: 245px;
    width: 540px;
    height: 309px;
    border-radius: 10px;
    overflow: hidden;
    border-bottom: 3px solid var(--sky);
    box-shadow: 0 14px 30px rgba(0,0,0,.28);
  }
  .card--front { left: 40px; background: var(--white); }
  .card--back {
    left: 620px;
    background: radial-gradient(ellipse at 35% 30%, var(--charcoal-light), var(--charcoal) 70%);
  }
  .front-panel {
    position: absolute;
    inset: 0;
  }
  .brand {
    position: absolute;
    left: 28px;
    top: 86px;
    width: 190px;
  }
  .brand-name {
    font-family: "Roboto", sans-serif;
    font-weight: 700;
    font-size: 64px;
    letter-spacing: 6px;
    line-height: 1;
    color: var(--logo-grey);
    display: flex;
    align-items: center;
    gap: 12px;
  }
  .brand-dot {
    width: 14px;
    height: 14px;
    border-radius: 50%;
    background: var(--sky);
  }
  .brand-tagline {
    margin-top: 12px;
    font-family: "Roboto Condensed", sans-serif;
    font-size: 12.5px;
    line-height: 1.35;
    letter-spacing: .4px;
    color: var(--royal);
  }
  .brand .brand-tagline span { display: block; }
  .contact {
    position: absolute;
    right: 26px;
    top: 70px;
    width: 210px;
    text-align: right;
    color: var(--ink-light);
  }
  .contact-name {
    font-family: "Roboto Condensed", sans-serif;
    font-weight: 700;
    font-size: 19px;
    line-height: 1.15;
    color: var(--sky);
    margin: 0 0 10px;
  }
  .contact-line {
    display: flex;
    justify-content: flex-end;
    align-items: center;
    gap: 7px;
    font-size: 13px;
    margin: 4px 0;
  }
  .contact-line svg { width: 12px; height: 12px; fill: var(--sky); }
  .contact-email { margin-top: 14px; font-size: 12.5px; }
  .back-brand {
    position: absolute;
    left: 0; right: 0;
    top: 96px;
    text-align: center;
  }
  .back-brand .brand-name {
    justify-content: center;
    font-size: 82px;
    color: var(--silver);
  }
  .back-brand .brand-tagline {
    margin-top: 16px;
    font-size: 15px;
    letter-spacing: 1px;
    color: var(--ink-light);
  }
</style>
</head>
<body>
<main class="canvas">

  <section class="card card--front" aria-label="Frente de la tarjeta">
    <svg class="front-panel" viewBox="0 0 540 309" preserveAspectRatio="none" aria-hidden="true">
      <defs>
        <linearGradient id="darkPanel" x1="0" y1="0" x2="1" y2="1">
          <stop offset="0" stop-color="#1f1f20"/>
          <stop offset=".55" stop-color="#3c3c3e"/>
          <stop offset="1" stop-color="#1d1d1e"/>
        </linearGradient>
      </defs>
      <polygon points="318,0 540,0 540,309 198,309" fill="url(#darkPanel)"/>
      <line x1="313" y1="0" x2="193" y2="309" stroke="#9a9a9c" stroke-width="3"/>
      <line x1="307" y1="0" x2="187" y2="309" stroke="#1f3aa8" stroke-width="3"/>
      <line x1="302" y1="0" x2="182" y2="309" stroke="#1e8fd8" stroke-width="1.5"/>
    </svg>

    <div class="brand">
      <div class="brand-name"><span>KRV</span><span class="brand-dot"></span></div>
      <div class="brand-tagline"><span>FABRICACION Y DISTRIBUCION</span><span>DE TORNILLOS</span></div>
    </div>

    <div class="contact">
      <p class="contact-name">Lic. Mariela Ortega Ruiz</p>
      <div class="contact-line">Cotizaciones en</div>
      <div class="contact-line">5550192034
        <svg viewBox="0 0 24 24"><path d="M6.6 10.8a15 15 0 0 0 6.6 6.6l2.2-2.2a1 1 0 0 1 1-.25 11.4 11.4 0 0 0 3.6.57 1 1 0 0 1 1 1V20a1 1 0 0 1-1 1A17 17 0 0 1 3 4a1 1 0 0 1 1-1h3.5a1 1 0 0 1 1 1c0 1.25.2 2.45.57 3.57a1 1 0 0 1-.25 1z"/></svg>
      </div>
      <div class="contact-line">5550187721
        <svg viewBox="0 0 24 24"><path d="M7 2h10a2 2 0 0 1 2 2v16a2 2 0 0 1-2 2H7a2 2 0 0 1-2-2V4a2 2 0 0 1 2-2zm0 3v13h10V5z"/></svg>
      </div>
      <div class="contact-line contact-email">krv.ventas@correo-mx.com
        <svg viewBox="0 0 24 24"><path d="M3 5h18v14H3zm2 2v.5l7 4.5 7-4.5V7z"/></svg>
      </div>
    </div>
  </section>

  <section class="card card--back" aria-label="Reverso de la tarjeta">
    <div class="back-brand">
      <div class="brand-name"><span>KRV</span></div>
      <div class="brand-tagline">FABRICACION Y DISTRIBUCION DE TORNILLOS</div>
    </div>
  </section>

</main>
</body>
</html>
```